New signage for apartment community in the Pacific Northwest

Signage for an apartment community in the Pacific Northwest. It should have a contemporary northwest vibe with a fresh exciting feeling. We are open to the colors cayenne, white, charcoal and a splash of lime green. Sign to have the name 'VOLTE' with the address number 28351 smaller underneath. sign can include a shape under the name or a feeling of energy in the shape of the name.

Target Market(s)

Young urban professionals

Industry/Entity Type

Real Estate Development

Requirements
Must have
• eyecatching
Should not have
• anything too cute or too busy

```html
<!DOCTYPE html>
<html lang="en">
<head>
<meta charset="utf-8">
<title>VOLTE – Community Sign</title>
<link rel="stylesheet" href="https://fonts.googleapis.com/css2?family=Playfair+Display:wght@700&family=Montserrat:wght@500&display=swap">
<style>
  :root {
    --cayenne: #a50000;
    --white: #ffffff;
    --lime: #8cc400;
    --charcoal-dark: #383838;
    --charcoal-light: #7a7a7a;
  }
  html, body {
    margin: 0;
    padding: 0;
    width: 796px;
    height: 1200px;
    overflow: hidden;
  }
  .canvas {
    position: relative;
    width: 796px;
    height: 1200px;
    background: linear-gradient(135deg, var(--charcoal-dark) 0%, var(--charcoal-light) 100%);
  }
  .sign {
    position: absolute;
    left: 59px;
    top: 374px;
    width: 677px;
    height: 452px;
    filter: drop-shadow(0 10px 14px rgba(0, 0, 0, 0.45));
  }
  .sign-panel { fill: var(--cayenne); }
  .sign-trim {
    fill: none;
    stroke: var(--white);
    stroke-width: 2;
  }
  .sign-ornament { fill: var(--white); }
  .sign-name {
    font-family: "Playfair Display", Georgia, serif;
    font-weight: 700;
    font-size: 240px;
    fill: var(--white);
  }
  .address-band { fill: var(--lime); }
  .address-band-edge {
    fill: none;
    stroke: var(--white);
    stroke-width: 2;
  }
  .address-text {
    font-family: "Montserrat", Arial, sans-serif;
    font-weight: 500;
    font-size: 42px;
    fill: var(--white);
  }
</style>
</head>
<body>
<main class="canvas">
  <svg class="sign" viewBox="0 0 903 603" xmlns="http://www.w3.org/2000/svg">
    <path class="sign-panel" d="M0 120 H133 V70 L450 0 L770 70 V120 H903 V603 H0 Z"/>
    <path class="sign-trim" d="M16 136 H149 V82 L450 15 L754 82 V136 H887 V587 H16 Z"/>
    <path class="sign-trim" d="M23 143 H156 V88 L450 23 L747 88 V143 H880 V580 H23 Z"/>
    <rect class="sign-ornament" x="302" y="100" width="300" height="60" rx="30" role="img" aria-label="White flourish scroll ornament"/>
    <text class="sign-name" x="451" y="385" text-anchor="middle" textLength="735" lengthAdjust="spacingAndGlyphs">VOLTE</text>
    <rect class="address-band" x="85" y="432" width="733" height="71" rx="35.5"/>
    <path class="address-band-edge" d="M100 500 Q120 505 130 505 H775 Q810 505 818 470"/>
    <text class="address-text" x="451" y="482" text-anchor="middle">28351,Pacific Northwest</text>
  </svg>
</main>
</body>
</html>
```